Larkspur Talent IT Recruiting firm needs a business card design for Recruiters, Sourcers, and Account

We need business cards that allow us to change all contact info, names, titles (Recruiter, Sourcer, Account Manager, Director, CEO, etc) per person since we have three offices, in three cities, Phoenix, Austin, and Las Vegas. We do recruiting and contractors for IT positions (Developers, Architects, Software Engineers, Security Engineers, Help Desk, DBAs, PMs, Scrum Masters, etc.) Our client companies are very diverse from Meridian 100 to silicone Valley type start-ups.

So, while we what hip, techie, and quirky, it still needs to be professional. Primary color we use is blue, with silver as a secondary color.

Target Market(s)

IT, Technology

Industry/Entity Type

Business

Contact Information for Business Card

Company name: Larkspur Talent, Inc.
Website: www.larkspurtalent.example
Logos for Careerloop, Blipster, and Myriada

Name, Title, Office Number, Cell Number, email

Font styles to use
Serif
Sans Serif

Colors
0455a3
d5d5d5

Requirements
Nice to have
• The grey I selected below is not necessary - but, would like silver included. I included a card design (File 3: LTI early trial example.jpg) that I had started on. It's very rough, and not quite what we're looking for, but what we did like is the logo, big, maybe a bit faded, off center, goes out of frame, etc. Still looking for other ideas - you are the pros! But, just an idea of a design element we liked.

```html
<!DOCTYPE html>
<html lang="en">
<head>
<meta charset="utf-8">
<title>Larkspur Talent Business Card</title>
<link href="https://fonts.googleapis.com/css2?family=Alegreya+Sans:wght@400;500&display=swap" rel="stylesheet">
<style>
  :root {
    --bg: #1c1c1c;
    --card-white: #ffffff;
    --card-edge: #4a4a4a;
    --back-grey: #575757;
    --back-grey-low: #646464;
    --brand-blue: #0a7cc8;
    --brand-blue-deep: #0455a3;
    --text-light: #ffffff;
    --faint: rgba(255,255,255,0.12);
  }
  html, body {
    margin: 0; padding: 0;
    width: 1200px; height: 907px;
    overflow: hidden;
    background: var(--bg);
  }
  .canvas { position: relative; width: 1200px; height: 907px; }

  .card { position: absolute; left: 300px; width: 600px; overflow: hidden; }

  /* Front */
  .card-front { top: 98px; height: 342px; background: var(--card-white); }
  .card-front .edge-band {
    position: absolute; left: 0; right: 0; bottom: 0; height: 12px;
    background: var(--card-edge);
  }
  .social-list {
    position: absolute; top: 28px; right: 22px;
    display: flex; gap: 10px;
    font-family: "Alegreya Sans", sans-serif; font-size: 11px; color: var(--brand-blue-deep);
  }
  .social-item { display: flex; align-items: center; gap: 4px; }
  .social-item .square { width: 9px; height: 9px; background: var(--brand-blue); }

  .brand-name {
    position: absolute; left: 0; right: 0; top: 150px;
    display: flex; justify-content: center; align-items: center; gap: 14px;
    font-family: "Alegreya Sans", sans-serif; font-weight: 500;
    font-size: 38px; letter-spacing: 3px; color: var(--brand-blue-deep); line-height: 1;
  }
  .brand-name .mark-circle {
    width: 34px; height: 34px; border-radius: 50%; background: var(--brand-blue-deep);
  }

  /* Back */
  .card-back {
    top: 475px; height: 343px;
    background: linear-gradient(180deg, var(--back-grey) 0%, var(--back-grey) 45%, var(--back-grey-low) 100%);
  }
  .decor-circle {
    position: absolute; left: 254px; top: 0; width: 320px; height: 320px;
  }
  .name-tab {
    position: absolute; left: 0; top: 140px; width: 10px; height: 54px;
    background: var(--text-light); border-radius: 0 6px 6px 0;
  }
  .person { position: absolute; left: 33px; top: 137px; font-family: "Alegreya Sans", sans-serif; color: var(--text-light); }
  .person-name { font-size: 27px; font-weight: 400; margin: 0; line-height: 1.1; }
  .person-title { font-size: 19px; margin: 5px 0 0; }
  .contact-list {
    position: absolute; left: 29px; top: 220px; margin: 0; padding: 0; list-style: none;
    font-family: "Alegreya Sans", sans-serif; font-size: 16px; color: var(--text-light);
  }
  .contact-list li { display: flex; align-items: center; height: 22.7px; }
  .contact-list svg { width: 14px; height: 14px; margin-right: 10px; fill: var(--text-light); }
</style>
</head>
<body>
<div class="canvas">

  <section class="card card-front">
    <div class="social-list">
      <span class="social-item"><span class="square"></span>Careerloop</span>
      <span class="social-item"><span class="square"></span>Blipster</span>
      <span class="social-item"><span class="square"></span>Myriada</span>
    </div>
    <div class="brand-name"><span class="mark-circle"></span><span>LARKSPUR TALENT</span></div>
    <div class="edge-band"></div>
  </section>

  <section class="card card-back">
    <svg class="decor-circle" viewBox="0 0 320 320" role="img" aria-label="Large faint brand circle decoration">
      <circle cx="160" cy="166" r="150" fill="var(--faint)"/>
    </svg>
    <div class="name-tab"></div>
    <div class="person">
      <p class="person-name">Dana Whitfield</p>
      <p class="person-title">Manager</p>
    </div>
    <ul class="contact-list">
      <li><svg viewBox="0 0 16 16"><path d="M4 1l3 3-2 2c1 2 3 4 5 5l2-2 3 3-2 3C7 15 1 9 1 3z"/></svg>555-014-2270</li>
      <li><svg viewBox="0 0 16 16"><path d="M4 0h8v16H4zM5.5 2v9h5V2z"/></svg>555-019-8834</li>
      <li><svg viewBox="0 0 16 16"><path d="M1 3h14v10H1zM2 4l6 5 6-5z"/></svg>info@larkspurtalent.example</li>
      <li><svg viewBox="0 0 16 16"><path d="M8 1a7 7 0 100 14A7 7 0 008 1zm0 1.3c.9 1 1.5 2.6 1.6 4.2H6.4C6.5 4.9 7.1 3.3 8 2.3zM2.3 7.5h2.8c.1 1.6.5 3 1.2 4.1a5.7 5.7 0 01-4-4.1zm0-1a5.7 5.7 0 014-4.1C5.6 3.5 5.2 4.9 5.1 6.5zm4.1 1h3.2c-.1 1.6-.7 3.2-1.6 4.2-.9-1-1.5-2.6-1.6-4.2zm4.5 0h2.8a5.7 5.7 0 01-4 4.1c.7-1.1 1.1-2.5 1.2-4.1zm0-1c-.1-1.6-.5-3-1.2-4.1a5.7 5.7 0 014 4.1z"/></svg>www.larkspurtalent.example</li>
    </ul>
  </section>

</div>
</body>
</html>
```